Card front cover, made up of words and statements, similar to the front of a tovarique bag.

I'm looking to design the front of a card or post card I will use in my business. I want to use a mash up of words and statements and sentences to inspire my audience. The card should be visually nice and use various fonts. My business inspires kids to set goals and dream big. You can use the "moon" shape as seen in my logo, but stick to mostly the words and statements listed on the attached word document or other similar statements you find, the shorter statements tend to look better. I'm interested to see a use of different fonts and sizes. All with a "modern" look and feel.

Target Market(s)

parents of children ages 8-12

Industry/Entity Type

Party space: specifically slumber parties

Font styles to use
Other font styles liked:
• Avenir Next LT pro

Colors
FFC000
F8CF3A
FAE287
FDF2CF
FEFAEE

Requirements
Must have
• The use of the "moon" logo and the words: Sleep Less, Dream More
Nice to have
• I made a long list of inspirational quotes to use, they don't all need to be used but that is the idea I'm looking for. After looking at designs the long sentences do NOT work as well. Please either shorten them or find other similar statements.
Should not have
• color, please use the yellow as shown in my moon logo, black and white

```html
<!DOCTYPE html>
<html lang="en">
<head>
<meta charset="utf-8">
<title>Sleep Less, Dream More – Card Front</title>
<link rel="stylesheet" href="https://fonts.googleapis.com/css2?family=Playfair+Display:wght@400;700;900&family=Libre+Baskerville:wght@400;700&family=Pathway+Gothic+One&family=Open+Sans:wght@400&family=Cormorant+Garamond:wght@500;600&family=Merriweather:wght@700;900&display=swap">
<style>
  :root {
    --ink: #333333;
    --sun: #FFC000;
    --gold: #F8CF3A;
    --butter: #FAE287;
    --glow: #FFF35C;
    --page: #FFFFFF;
  }
  * { margin: 0; padding: 0; box-sizing: border-box; }
  html, body { width: 1200px; height: 933px; overflow: hidden; background: var(--page); }
  .card-canvas { position: relative; width: 1200px; height: 933px; background: var(--page); }
  .card-face {
    position: absolute; left: 64px; top: 74px; width: 1069px; height: 801px;
    background: linear-gradient(160deg, var(--gold) 0%, #FFD21F 45%, var(--glow) 100%);
    overflow: hidden;
  }
  .backdrop-disc { position: absolute; left: 0; top: 0; width: 1069px; height: 801px; }
  .quote { position: absolute; color: var(--ink); white-space: nowrap; }

  .realities { left: 29px; top: 32px; font: 700 23px/36px "Libre Baskerville", serif; letter-spacing: 0.5px; }
  .stat-bar {
    position: absolute; left: 28px; top: 125px; width: 499px; height: 38px;
    background: var(--ink); color: var(--sun);
    font: 700 12px/38px "Merriweather", serif; padding-left: 12px; white-space: nowrap;
  }
  .goals-deadline { left: 34px; top: 172px; font: 900 72px/75px "Playfair Display", serif; letter-spacing: 2px; word-spacing: 6px; }
  .action-left { left: 28px; top: 418px; font: 400 43px/48px "Pathway Gothic One", sans-serif; }
  .chase-left { left: 34px; top: 548px; font: 700 58px/75px "Libre Baskerville", serif; }

  .do-right {
    position: absolute; left: 572px; top: 25px; height: 446px; width: 30px;
    writing-mode: vertical-rl; transform: rotate(180deg);
    font: 400 26px/30px Arial, "Helvetica Neue", sans-serif; color: var(--ink);
    white-space: nowrap; text-align: center;
  }

  .chase-caps { left: 624px; top: 24px; font: 500 35px/39px "Cormorant Garamond", serif; letter-spacing: 1px; }
  .rule { position: absolute; left: 629px; width: 384px; height: 2px; background: var(--ink); }
  .rule-top { top: 107px; }
  .rule-mid { top: 304px; }
  .action-right { left: 625px; top: 114px; font: 400 20px/28px "Open Sans", sans-serif; }
  .sleep-less { left: 628px; top: 172px; font: 900 66px/63px "Playfair Display", serif; letter-spacing: 1px; }
  .dream-it { left: 634px; top: 310px; font: 400 34px/42px "Playfair Display", serif; }
  .energy-bar {
    position: absolute; left: 620px; top: 360px; width: 397px; height: 35px;
    background: var(--ink); color: var(--butter);
    font: 600 17px/35px "Cormorant Garamond", serif; text-align: center; letter-spacing: 0.5px;
  }

  .tilted { position: absolute; transform-origin: center; }
  .motivates-main {
    left: 421px; top: 490px; width: 560px; transform: rotate(-20deg);
    font: 400 40px/45px Arial, "Helvetica Neue", sans-serif; color: var(--ink); white-space: nowrap;
  }
  .dream-badge {
    left: 765px; top: 534px; width: 231px; height: 77px; transform: rotate(-22deg);
    background: var(--ink); color: var(--gold);
    font: 900 32px/77px "Merriweather", serif; text-align: center;
  }
  .dream-awake {
    left: 500px; top: 613px; width: 260px; transform: rotate(-20deg);
    font: 700 15px/21px "Merriweather", serif; color: var(--ink);
    letter-spacing: 2px; white-space: nowrap;
  }
  .motivates-small {
    left: 675px; top: 626px; width: 390px; transform: rotate(-20deg);
    font: 400 35px/40px Arial, "Helvetica Neue", sans-serif; color: var(--ink);
    text-align: center; white-space: nowrap;
  }
</style>
</head>
<body>
<div class="card-canvas">
  <main class="card-face">
    <svg class="backdrop-disc" viewBox="0 0 1069 801" aria-hidden="true">
      <circle cx="434" cy="391" r="378" fill="#FFFFFF" fill-opacity="0.22"/>
    </svg>

    <p class="quote realities">Never stop dreaming --- most realities<br>were once created from dreams.</p>
    <p class="stat-bar">You are almost twice as likely to reach your goals simply by writing them down.</p>
    <h2 class="quote goals-deadline">Goals are just<br>dreams with<br>a deadline</h2>
    <p class="quote action-left">What's one action I can take today<br>to make my goal feel more achievable?</p>
    <h2 class="quote chase-left">Don't follow<br>your dream<br>chase them!</h2>

    <p class="do-right">Do what is right, not what is easy</p>

    <p class="quote chase-caps">DON'T FOLLOW YOUR<br>DREAM CHASE THEM!</p>
    <div class="rule rule-top"></div>
    <p class="quote action-right">What's one action I can take today<br>to make my goal feel more achievable?</p>
    <h1 class="quote sleep-less">Sleep Less,<br>Dream More</h1>
    <div class="rule rule-mid"></div>
    <p class="quote dream-it">Dream it, wish it, do it</p>
    <p class="energy-bar">BE THE ENERGY YOU WANT TO ATTRACT</p>

    <p class="tilted motivates-main">What motivates you to keep<br>&nbsp;going when things get tough?</p>
    <p class="tilted dream-badge">Dream More</p>
    <p class="tilted dream-awake">A dream is not something<br>that happens while<br>you sleep, its what keeps<br>you awake and striving<br>for something greater<br>every day</p>
    <p class="tilted motivates-small">What motivates<br>you to keep going when<br>things get tough?</p>
  </main>
</div>
</body>
</html>
```